Storm Restoration Contractor needs a professional letterhead design

Looking for a professional letterhead design. Not looking for your cheapo MS Word standard ones that are readily available. Dont want it to be cookie cutter look like ones readily available online. We just recently changed our logo and want to freshen up all our documents. Our company handles restoring a property back to a pre-loss condition after a storm damages it. For example, wind, hail, flood, fire losses.

Target Market(s)

Property Owners, Homeowners, Property Owners, Commercial Property Owners, Property Management Companies

Industry/Entity Type

Construction Company

Requirements
Must have
• Professional, Use 1 of 2 logo options
• Storm Restoration, Roofing, Siding, Windows

```html
<!DOCTYPE html>
<html lang="en">
<head>
<meta charset="utf-8">
<title>Northgate Exteriors Letterhead</title>
<link rel="stylesheet" href="https://fonts.googleapis.com/css2?family=Open+Sans:wght@400;600&display=swap">
<style>
  :root {
    --backdrop: #e9eaec;
    --paper: #ffffff;
    --brand-blue: #1a6fc0;
    --brand-navy: #1f4f8f;
    --swoosh-grey: #e6e7e9;
    --mark-tint: #eef1f6;
    --ink: #2b2b2b;
  }
  * { box-sizing: border-box; margin: 0; padding: 0; }
  html, body {
    width: 1200px;
    height: 795px;
    overflow: hidden;
    background: var(--backdrop);
    font-family: "Open Sans", Arial, sans-serif;
  }
  .letterhead {
    position: absolute;
    left: 338px;
    top: 28px;
    width: 523px;
    height: 740px;
    background: var(--paper);
    box-shadow: 0 4px 18px rgba(0, 0, 0, 0.12);
    overflow: hidden;
  }
  .letterhead__decor {
    position: absolute;
    inset: 0;
    width: 100%;
    height: 100%;
  }
  .brand {
    position: absolute;
    left: 34px;
    top: 30px;
    display: flex;
    align-items: center;
    gap: 8px;
  }
  .brand__dot {
    width: 22px;
    height: 22px;
    border-radius: 50%;
    background: var(--brand-blue);
  }
  .brand__name {
    font-size: 13px;
    font-weight: 600;
    letter-spacing: 1.5px;
    text-transform: uppercase;
    color: var(--brand-blue);
    white-space: nowrap;
  }
  .contact {
    position: absolute;
    right: 34px;
    bottom: 58px;
    text-align: right;
    font-size: 9.5px;
    line-height: 1.5;
    color: var(--ink);
  }
  .contact__company,
  .contact__web { color: var(--brand-blue); }
  .contact__lines {
    display: flex;
    justify-content: flex-end;
    align-items: center;
    gap: 4px;
  }
  .contact__icon {
    width: 10px;
    height: 10px;
    flex: none;
  }
</style>
</head>
<body>
  <main class="letterhead">
    <svg class="letterhead__decor" viewBox="0 0 523 740" aria-hidden="true">
      <path fill="var(--swoosh-grey)" d="M523,70 C430,100 290,118 200,160 C130,194 65,226 0,252 L0,270 C72,242 135,210 208,176 C298,134 440,120 523,92 Z"/>
      <path fill="var(--brand-blue)" d="M523,52 C420,84 272,100 176,146 C104,182 50,210 0,230 L0,244 C58,222 112,194 182,160 C276,114 432,96 523,66 Z"/>
      <circle cx="262" cy="380" r="150" fill="none" stroke="var(--mark-tint)" stroke-width="26"/>
    </svg>

    <header class="brand">
      <span class="brand__dot"></span>
      <span class="brand__name">Northgate Exteriors</span>
    </header>

    <footer class="contact">
      <p class="contact__company">Northgate Exteriors</p>
      <p class="contact__address">2250 Harbor Ridge Drive, Fairview, CA 95014</p>
      <p class="contact__lines">
        <svg class="contact__icon" viewBox="0 0 10 10" aria-label="Phone"><circle cx="5" cy="5" r="5" fill="var(--brand-navy)"/><path d="M3 2.5h1.2l.5 1.3-.7.6a4 4 0 0 0 1.6 1.6l.6-.7 1.3.5V7A.6.6 0 0 1 6.9 7.5 4.6 4.6 0 0 1 2.5 3.1.6.6 0 0 1 3 2.5z" fill="#fff"/></svg>
        <span>(555) 014-2288</span>
        <svg class="contact__icon" viewBox="0 0 10 10" aria-label="Fax"><circle cx="5" cy="5" r="5" fill="var(--brand-navy)"/><rect x="2.6" y="3.8" width="4.8" height="2.8" fill="#fff"/><rect x="3.5" y="2.4" width="3" height="1.2" fill="#fff"/></svg>
        <span>(555) 014-2289</span>
        <svg class="contact__icon" viewBox="0 0 10 10" aria-label="Email"><circle cx="5" cy="5" r="5" fill="var(--brand-navy)"/><rect x="2.5" y="3.2" width="5" height="3.6" fill="#fff"/><path d="M2.5 3.2 5 5.2 7.5 3.2" fill="none" stroke="var(--brand-navy)" stroke-width=".6"/></svg>
        <span>info@northgateexteriors.com</span>
      </p>
      <p class="contact__web">www.northgateexteriors.com</p>
    </footer>
  </main>
</body>
</html>
```